Letterhead for a German Distribution/Manufacturing Company

We need a professional Letterhead in a unique Design.
not to playful.
The Letterhead has to show show that we are a international company with headquater in Germany.
all details like adress, Vat Tax Number, Bank Accout, Eori, email, Company number has to be on the Letterhead.
for example use: VAT TAX DE5470318 Bank Account: Kestrel Bank IBAN DE412058731ß204683 Swift: MORV0417352 EORI 3150428697 Company Number: HRB 51806 Adress: VOLMINTA UG Ahornweg 7 Postal Code 06384 City Lindenau Country: Germany Email: info@volminta-example.com
the design can be colored but doesnt have to be
Industry/Entity Type
Manufacturing and international distribution
Requirements
Must have
- show that we are a international company with headquater in Germany. our company infos and logo

```html
<!DOCTYPE html>
<html lang="en">
<head>
<meta charset="utf-8">
<title>VOLMINTA UG – Letterhead</title>
<link href="https://fonts.googleapis.com/css2?family=Open+Sans:wght@400;600&display=swap" rel="stylesheet">
<style>
  :root {
    --backdrop: #b9b9b9;
    --paper: #ffffff;
    --ink: #111111;
    --text: #3a3a3a;
    --muted: #555555;
    --signature-tone: #e4e4e4;
    --rule: #1a1a1a;
  }
  * { box-sizing: border-box; margin: 0; padding: 0; }
  html, body {
    width: 1200px; height: 800px; overflow: hidden;
    background: var(--backdrop);
    font-family: "Open Sans", sans-serif;
  }
  .letterhead {
    position: absolute; left: 330px; top: 18px;
    width: 540px; height: 764px;
    background: var(--paper);
    padding: 42px 48px 0 56px;
    color: var(--text);
    box-shadow: 0 4px 14px rgba(0,0,0,.18);
  }
  .brand {
    display: flex; align-items: center; gap: 12px;
    margin-left: -14px;
  }
  .brand-dot {
    width: 34px; height: 34px; border-radius: 50%;
    background: var(--ink);
  }
  .brand-name {
    font-weight: 600; font-size: 38px; letter-spacing: 1px;
    color: var(--ink); line-height: 1;
  }
  .salutation {
    margin-top: 22px; font-size: 10px; color: var(--ink);
  }
  .body-copy {
    margin-top: 14px; width: 400px;
    font-size: 8px; line-height: 1.3;
  }
  .body-copy p + p { margin-top: 10px; }
  .closing {
    margin-top: 30px; font-size: 8px; color: var(--muted);
  }
  .signature {
    display: block; margin-top: 6px;
    width: 110px; height: 18px;
    background: var(--signature-tone); border-radius: 3px;
  }
  .signatory {
    margin-top: 4px; font-size: 16px; color: var(--muted); letter-spacing: .3px;
  }
  .footer {
    position: absolute; left: 30px; right: 20px; bottom: 40px;
    display: flex; align-items: flex-start; justify-content: space-between;
    font-size: 7px; line-height: 1.5; color: var(--ink);
    white-space: nowrap;
  }
  .footer-col { padding: 0 6px; }
  .footer-divider {
    width: 1px; height: 44px; background: var(--rule);
    transform: skewX(-14deg); flex: none;
  }
  .contact-line { display: flex; align-items: center; gap: 4px; }
  .contact-line svg { width: 7px; height: 7px; flex: none; fill: var(--ink); }
</style>
</head>
<body>
  <main class="letterhead">
    <header class="brand">
      <span class="brand-dot" aria-hidden="true"></span>
      <span class="brand-name">VOLMINTA</span>
    </header>

    <p class="salutation">Dear Mr. Halvorsen</p>

    <section class="body-copy">
      <p>Lorem Ipsum is simply dummy text of the printing and typesetting industry. Lorem Ipsum has been the industry's standard dummy text ever since the 1500s, when an unknown printer took a galley of type and scrambled it to make a type specimen book. It has survived not only five centuries, but also the leap into electronic typesetting, remaining essentially unchanged. It was popularised in the 1960s with the release of Letraset sheets containing Lorem Ipsum passages</p>
      <p>Lorem Ipsum is simply dummy text of the printing and typesetting industry. Lorem Ipsum has been the industry's standard dummy text ever since the 1500s, when an unknown printer took a galley of type and scrambled it to make a type specimen book. It has survived not only five centuries, but also the leap into electronic typesetting, remaining essentially unchanged. It was popularised in the 1960s with the release of Letraset sheets containing Lorem Ipsum passages</p>
      <p>Lorem Ipsum is simply dummy text of the printing and typesetting industry. Lorem Ipsum has been the industry's standard dummy text ever since the 1500s, when an unknown printer took a galley of type and scrambled it to make a type specimen book. It has survived not only five centuries, but also the leap into electronic typesetting, remaining essentially unchanged. It was popularised in the 1960s with the release of Letraset sheets containing Lorem Ipsum passages</p>
    </section>

    <section class="sign-off">
      <p class="closing">Sincerely</p>
      <span class="signature" role="img" aria-label="Handwritten signature of Tobias Wendt"></span>
      <p class="signatory">TOBIAS WENDT</p>
    </section>

    <footer class="footer">
      <div class="footer-col">Ahornweg 7,<br>Lindenau, Germany</div>
      <span class="footer-divider"></span>
      <div class="footer-col">VAT TAX : DE5470318<br>IBAN : DE412058731ß204683<br>Swift: MORV0417352<br>EORI : 3150428697</div>
      <span class="footer-divider"></span>
      <div class="footer-col">Company Number : HRB 51806<br>Postal Code : 06384 City Lindenau<br>Country : Germany</div>
      <span class="footer-divider"></span>
      <div class="footer-col">
        <div class="contact-line"><svg viewBox="0 0 10 10"><path d="M2 0.5l2 2-1 1.3c.6 1.3 1.6 2.3 2.9 2.9l1.3-1 2 2-1.2 1.8C4.5 9.3.7 5.5.2 1.7z"/></svg>+49 3724 55 81 90</div>
        <div class="contact-line"><svg viewBox="0 0 10 10"><path d="M0 2h10v6H0z M0 2l5 3.5L10 2" /></svg>info@volminta-example.com</div>
        <div class="contact-line"><svg viewBox="0 0 10 10"><circle cx="5" cy="5" r="5"/></svg>www.volminta-example.com</div>
      </div>
    </footer>
  </main>
</body>
</html>
```